Business card for my new company (Accounting firm)

I need a business card for my new business Brightwell Advisory and Ledger SA. Our services are accounting, tax, audit and financial management. Our customers are small companies, start-ups and new companies. The final design has to show financial security, trust and growth. Please find our logo attached to the business card. Text for the business card: Brightwell Advisory and Ledger SA Tomas Varenholt Director and Founder Certified Accountant Tel. 022 418 57 34 tv@clairevalconseil.ch www.clairevalconseil.ch Rue des Vergières 27 1201 Geneva
Target Market(s)
Our customers are small companies, start-ups and new companies.
Industry/Entity Type
Finance And Accounting
Contact Information for Business Card
Claireval Conseil et Comptes SA
Tomas Varenholt
Directeur et Fondateur
Expert-comptable diplômé
Tél. 022 418 57 34
tv@clairevalconseil.ch
www.clairevalconseil.ch
Rue des Vergières 27
1201 Genève

```html
<!DOCTYPE html>
<html lang="fr">
<head>
<meta charset="utf-8">
<title>Claireval Conseil et Comptes SA – Carte de visite</title>
<link rel="stylesheet" href="https://fonts.googleapis.com/css2?family=Roboto:wght@400;500;700&display=swap">
<style>
  :root {
    --backdrop: #e4e5e7;
    --brand-blue: #2a94cf;
    --brand-blue-deep: #1c6aa3;
    --brand-navy: #1d5a8e;
    --ink-dark: #3a3d42;
    --ink-grey: #54585e;
    --paper: #f7f8f8;
    --white: #ffffff;
  }
  * { box-sizing: border-box; margin: 0; padding: 0; }
  html, body { width: 1200px; height: 726px; overflow: hidden; }
  body {
    background: var(--backdrop);
    font-family: "Roboto", Arial, sans-serif;
    position: relative;
  }
  .card {
    position: absolute;
    top: 214px;
    width: 520px;
    height: 297px;
    border-radius: 4px;
    overflow: hidden;
    box-shadow: 0 10px 26px rgba(0,0,0,0.16);
  }
  /* Front */
  .card--front {
    left: 53px;
    background: linear-gradient(160deg, var(--brand-blue) 0%, var(--brand-blue-deep) 100%);
    color: var(--white);
    display: flex;
    flex-direction: column;
    align-items: center;
    justify-content: center;
    text-align: center;
  }
  .wordmark {
    display: flex;
    align-items: center;
    gap: 12px;
    font-weight: 500;
  }
  .wordmark__square {
    width: 34px; height: 34px;
    background: currentColor;
  }
  .wordmark__name { line-height: 1.05; text-align: left; }
  .wordmark__name span { display: block; }
  .card--front .wordmark { font-size: 34px; }
  .card--front .wordmark__name span + span { font-size: 15px; letter-spacing: 3px; text-transform: uppercase; margin-top: 4px; }
  .front__url {
    margin-top: 34px;
    font-size: 15px;
    font-weight: 500;
    letter-spacing: 0.3px;
  }
  /* Back */
  .card--back {
    left: 627px;
    background: var(--paper);
  }
  .back__wave { position: absolute; inset: 0; }
  .card--back .wordmark {
    position: absolute;
    top: 30px;
    right: 28px;
    color: var(--ink-dark);
    font-size: 28px;
  }
  .card--back .wordmark__square { width: 26px; height: 26px; background: var(--brand-blue); }
  .card--back .wordmark__name span + span { font-size: 12px; letter-spacing: 2.4px; text-transform: uppercase; margin-top: 3px; }
  .person { position: absolute; left: 34px; top: 92px; }
  .person__name { font-size: 22px; font-weight: 700; color: var(--brand-navy); }
  .person__role { font-size: 12.5px; color: var(--ink-grey); line-height: 1.3; margin-top: 5px; }
  .contact { position: absolute; left: 34px; top: 186px; list-style: none; }
  .contact li {
    display: flex; align-items: center; gap: 10px;
    font-size: 13.5px; color: var(--ink-dark); line-height: 1.55;
  }
  .contact svg { width: 13px; height: 13px; fill: var(--brand-navy); flex: none; }
  .address {
    position: absolute;
    right: 22px;
    top: 214px;
    text-align: right;
    color: var(--white);
    font-size: 13px;
    line-height: 1.45;
    font-style: normal;
  }
</style>
</head>
<body>

<section class="card card--front" aria-label="Recto">
  <div class="wordmark">
    <span class="wordmark__square"></span>
    <span class="wordmark__name"><span>Claireval</span><span>Conseil et Comptes</span></span>
  </div>
  <p class="front__url">www.clairevalconseil.ch</p>
</section>

<section class="card card--back" aria-label="Verso">
  <svg class="back__wave" viewBox="0 0 520 297" preserveAspectRatio="none" aria-hidden="true">
    <path d="M200 297 C300 285 370 170 520 90 L520 297 Z" fill="#2a94cf"/>
    <path d="M270 297 C380 280 440 210 520 160 L520 297 Z" fill="#1d6aa5"/>
    <path d="M165 292 C280 280 345 162 520 72 L520 82 C360 170 295 284 165 292 Z" fill="#3a3d42"/>
  </svg>

  <div class="wordmark">
    <span class="wordmark__square"></span>
    <span class="wordmark__name"><span>Claireval</span><span>Conseil et Comptes</span></span>
  </div>

  <div class="person">
    <h1 class="person__name">Tomas Varenholt</h1>
    <p class="person__role">Directeur et Fondateur<br>Expert-comptable diplômé</p>
  </div>

  <ul class="contact">
    <li>
      <svg viewBox="0 0 24 24"><path d="M6.6 10.8a15.1 15.1 0 0 0 6.6 6.6l2.2-2.2c.3-.3.7-.4 1-.2 1.1.4 2.3.6 3.6.6.6 0 1 .4 1 1V20c0 .6-.4 1-1 1A17 17 0 0 1 3 4c0-.6.4-1 1-1h3.5c.6 0 1 .4 1 1 0 1.3.2 2.5.6 3.6.1.3 0 .7-.2 1z"/></svg>
      022 418 57 34
    </li>
    <li>
      <svg viewBox="0 0 24 24"><path d="M2 5h20v14H2z M3.5 6.5 12 13l8.5-6.5" fill="none" stroke="#1d5a8e" stroke-width="2.4"/></svg>
      tv@clairevalconseil.ch
    </li>
    <li>
      <svg viewBox="0 0 24 24"><circle cx="12" cy="12" r="9.5" fill="none" stroke="#1d5a8e" stroke-width="2.2"/><path d="M2.5 12h19M12 2.5c3 3 3 16 0 19M12 2.5c-3 3-3 16 0 19" fill="none" stroke="#1d5a8e" stroke-width="1.8"/></svg>
      www.clairevalconseil.ch
    </li>
  </ul>

  <address class="address">
    Rue des Vergières<br>27 1201 Genève
  </address>
</section>

</body>
</html>
```